Help design website for "Brightwater Civic Advisors" to advance the common good

Here is the Google doc link that lays out the design:

https://files.plumrivet.example/sheet/d/7QmTzR2wLx9KpVbN4hJcY8sEaUoFdG3iXkMnPq5rWt6/edit?usp=sharing

Here is the Google drive folder with the logos and photos: https://vault.plumrivet.example/open?id=4HkWp9LzQe2TxRvN8mBaYc3DsUoJfG6

The testimonials are being gathered and will be shared by Friday, 1/4.

The winner will also have to migrate the coding files to my hosting site.

Thank you for your help! Looking forward to seeing your designs.

Target Market(s)

Prospective clients

Industry/Entity Type

Non Profit

Coding

Coded - Design and coding required

Number of Pages Required

5+ page

Requirements
Must have
• Noted in the Google doc regarding layout.
Nice to have

```html
<!DOCTYPE html>
<html lang="en">
<head>
<meta charset="utf-8">
<title>Brightwater Civic Advisors — Services &amp; Testimonials</title>
<link rel="stylesheet" href="https://fonts.googleapis.com/css2?family=Poppins:wght@600;700&family=PT+Sans:wght@400;700&display=swap">
<style>
  :root {
    --brand-blue: #3d8ad0;
    --ink: #1f1f24;
    --body: #2e2e33;
    --footer: #25272f;
    --pattern: #eceef1;
    --white: #ffffff;
  }
  * { margin: 0; padding: 0; box-sizing: border-box; }
  html, body { width: 760px; height: 1200px; overflow: hidden; background: var(--white); }
  body { position: relative; font-family: "PT Sans", sans-serif; color: var(--body); }

  .site-header { position: absolute; top: 0; left: 0; width: 760px; height: 78px; background: var(--brand-blue); }
  .brand { position: absolute; left: 90px; top: 18px; display: flex; align-items: center; gap: 10px; color: var(--white); }
  .brand-mark { width: 12px; height: 12px; background: var(--white); }
  .brand-name { font-family: "Poppins", sans-serif; font-weight: 600; font-size: 15px; letter-spacing: 3px; line-height: 1.15; text-transform: uppercase; width: 180px; }
  .cta { position: absolute; left: 466px; top: 13px; width: 202px; height: 27px; border: 2px solid var(--white); color: var(--white); font-family: "Poppins", sans-serif; font-weight: 700; font-size: 8.5px; display: flex; align-items: center; justify-content: center; text-transform: uppercase; }
  .main-nav { position: absolute; right: 92px; top: 55px; display: flex; gap: 20px; font-family: "Poppins", sans-serif; font-weight: 700; font-size: 8.5px; color: var(--white); text-transform: uppercase; }
  .main-nav .active { border-bottom: 1px solid var(--white); padding-bottom: 1px; }

  .hero { position: absolute; top: 78px; left: 0; width: 760px; height: 346px; background: radial-gradient(ellipse at 60% 30%, #7a6350 0%, #3d3128 45%, #120e0c 100%); }
  .hero-edge { position: absolute; top: 350px; left: 0; }

  .intro { position: absolute; top: 414px; left: 120px; width: 520px; text-align: center; }
  .intro h1 { font-family: "Poppins", sans-serif; font-weight: 700; font-size: 17px; color: var(--ink); margin-bottom: 14px; }
  .intro p { font-size: 10px; line-height: 1.32; }

  .card { position: absolute; top: 530px; width: 278px; height: 417px; background: var(--white); box-shadow: 0 2px 8px rgba(0,0,0,0.12); }
  .card.left { left: 90px; }
  .card.right { left: 390px; }
  .card-photo { position: absolute; left: 0; bottom: 190px; width: 100%; display: flex; align-items: flex-end; padding: 0 14px 8px; }
  .card.left .card-photo { height: 187px; background: linear-gradient(180deg, #8fb0c8 0%, #5b6670 40%, #2c2e30 100%); top: 40px; }
  .card.right .card-photo { height: 227px; top: 0; background: linear-gradient(180deg, #6b5a4a 0%, #3a3836 50%, #1d1e22 100%); }
  .card-caption { font-family: "Poppins", sans-serif; font-weight: 700; font-size: 9.5px; line-height: 1.2; color: var(--white); text-transform: uppercase; }
  .card-quote { position: absolute; top: 244px; left: 32px; width: 232px; font-size: 8.8px; line-height: 1.3; color: var(--body); }
  .q-open, .q-close { font-family: "Poppins", sans-serif; font-weight: 700; font-size: 20px; color: var(--ink); line-height: 1; position: absolute; }
  .q-open { left: -14px; top: -8px; }
  .q-close { right: 60px; bottom: -18px; }
  .card-author { position: absolute; left: 32px; width: 230px; font-size: 8.8px; line-height: 1.3; }
  .card.left .card-author { top: 374px; }
  .card.right .card-author { left: 34px; top: 372px; }
  .card-author strong { font-weight: 700; color: var(--ink); }

  .pattern-band { position: absolute; top: 950px; left: 0; width: 760px; height: 115px; background: linear-gradient(180deg, var(--white) 0%, var(--pattern) 60%); }

  .site-footer { position: absolute; top: 995px; left: 0; }
  .footer-brand { position: absolute; left: 92px; top: 1092px; display: flex; align-items: center; gap: 12px; color: var(--white); }
  .footer-brand .brand-mark { width: 14px; height: 14px; background: var(--brand-blue); }
  .footer-brand .brand-name { font-size: 18px; letter-spacing: 4px; width: 240px; }
  .footer-divider { position: absolute; left: 388px; top: 1077px; width: 1px; height: 90px; background: #4a4c55; }
  .footer-menu { position: absolute; left: 425px; top: 1087px; color: var(--white); font-size: 7.5px; }
  .footer-menu h2 { font-family: "Poppins", sans-serif; font-weight: 700; font-size: 7.5px; text-transform: uppercase; margin-bottom: 12px; }
  .footer-links { display: flex; gap: 6px; text-transform: uppercase; }
  .footer-links span.sep { color: #9a9ca5; }
  .copyright { position: absolute; left: 426px; top: 1148px; color: var(--white); font-size: 7.5px; }
</style>
</head>
<body>
  <header class="site-header">
    <div class="brand">
      <span class="brand-mark"></span>
      <span class="brand-name">Brightwater Civic Advisors</span>
    </div>
    <div class="cta">Book a complimentary consultation</div>
    <nav class="main-nav">
      <span>About</span>
      <span class="active">Services &amp; Testimonials</span>
      <span>Media &amp; Impact</span>
      <span>Contact</span>
    </nav>
  </header>

  <div class="hero" role="img" aria-label="Photo of Maya speaking at a podium in front of a projected slide"></div>
  <svg class="hero-edge" width="760" height="80" viewBox="0 0 760 80">
    <polygon points="0,70 380,8 760,70 760,80 0,80" fill="#3d8ad0"/>
    <polygon points="0,78 380,16 760,78 760,80 0,80" fill="#ffffff"/>
  </svg>

  <section class="intro">
    <h1>Program Design, Implementation, &amp; Evaluation</h1>
    <p>Maya has launched several programs that take into account best practices, as well as particular institutional cultures, participant demographics, and geographical location. The evaluation data of these programs have demonstrated their impact, and she has secured funding and developed key partnerships for program expansion.</p>
  </section>

  <article class="card left">
    <div class="card-photo" role="img" aria-label="Photo of Maya with a large student cohort cheering by the lakefront">
      <p class="card-caption">Maya with the City Bound pre-orientation civic engagement program cohort</p>
    </div>
    <blockquote class="card-quote">
      <span class="q-open">&ldquo;</span>
      Maya has an uncanny ability to combine social change theory and real-world practice in truly compelling ways. For five years at Midlake University, I saw first-hand how Maya inspired legions of students, created innovative programs, and transformed relationships with community stakeholders. Best of all, she did it with integrity, smarts, enthusiasm and a warm, infectious spirit.
      <span class="q-close">&rdquo;</span>
    </blockquote>
    <p class="card-author"><strong>Daniel Reyes,</strong> VP, Chief Content Officer, WLMR</p>
  </article>

  <article class="card right">
    <div class="card-photo" role="img" aria-label="Photo of Maya introducing a panel discussion in a lecture hall">
      <p class="card-caption">Maya introducing the panel discussion on health access in Chicago</p>
    </div>
    <p class="card-author"><strong>Rosa Delgado</strong> Senior Manager of Community Engagement, Lakeshore Scholars</p>
  </article>

  <div class="pattern-band" role="img" aria-label="Light decorative background band"></div>

  <svg class="site-footer" width="760" height="205" viewBox="0 0 760 205">
    <polygon points="0,68 380,1 760,68 760,205 0,205" fill="#25272f"/>
  </svg>
  <div class="footer-brand">
    <span class="brand-mark"></span>
    <span class="brand-name">Brightwater Civic Advisors</span>
  </div>
  <div class="footer-divider"></div>
  <nav class="footer-menu">
    <h2>Menu</h2>
    <div class="footer-links">
      <span>About</span><span class="sep">|</span>
      <span>Services &amp; Testimonials</span><span class="sep">|</span>
      <span>Media &amp; Impact</span><span class="sep">|</span>
      <span>Contact</span>
    </div>
  </nav>
  <p class="copyright">Copyrights @ 2019 All Rights Reserved</p>
</body>
</html>
```